Oil Field Service company needs professional business cards

Looking to clean up our current company business cards and look a little more professional. Brenwick Casing Services is a US based company that services the oil field. We deal with engineers, managers and oil rigs....................................................................................................................................................................................................................................................................................................................................................................................................

Target Market(s)

Oil and Gas professionals

Industry/Entity Type

Oil And Gas

Contact Information for Business Card

See attached photo as example

Font styles to use
Sans Serif

Colors
ec1f27

Requirements
Must have
• Company Logo, Name, Title, Cell, Office, Fax, Email.
• See attached photo
Nice to have
• External CRT, Internal CRT, Casing Crews, Torque Turn, Laydown Machine
Should not have
• Do not introduce any new pictures and keep it professional looking

```html
<!DOCTYPE html>
<html lang="en">
<head>
<meta charset="utf-8">
<title>Brenwick Casing Services – Business Card</title>
<link href="https://fonts.googleapis.com/css2?family=Roboto+Condensed:wght@400;700&display=swap" rel="stylesheet">
<style>
  :root {
    --brand-red: #d1201f;
    --slate: #3d5163;
    --paper: #f5f5f3;
    --white: #ffffff;
    --backdrop: #e4e4e4;
    --soft-text: #dfe5ea;
  }
  * { box-sizing: border-box; margin: 0; padding: 0; }
  html, body { width: 1200px; height: 576px; overflow: hidden; }
  body {
    background: var(--backdrop);
    font-family: "Roboto Condensed", Arial, sans-serif;
    position: relative;
  }
  .card {
    position: absolute;
    width: 484px;
    height: 292px;
    border-radius: 6px;
    overflow: hidden;
  }
  .card-front { left: 82px; top: 139px; background: var(--brand-red); }
  .card-back { left: 602px; top: 139px; background: var(--slate); }

  .wordmark {
    position: absolute;
    left: 0; right: 0;
    text-align: center;
    font-weight: 700;
    text-transform: uppercase;
    line-height: 1;
  }
  .card-front .wordmark { top: 108px; color: var(--white); }
  .wordmark-name { display: block; font-size: 50px; letter-spacing: 1px; }
  .wordmark-tag { display: block; font-size: 14px; letter-spacing: 2.4px; margin-top: 12px; }

  .back-art { position: absolute; inset: 0; }
  .card-back .wordmark { left: 230px; right: 0; top: 44px; color: var(--slate); }
  .card-back .wordmark-name { font-size: 40px; }
  .card-back .wordmark-tag { font-size: 13px; margin-top: 14px; }

  .person { position: absolute; left: 18px; top: 129px; color: var(--white); }
  .person-name { font-size: 24px; font-weight: 400; line-height: 1; }
  .person-title { font-size: 12px; color: var(--soft-text); margin-top: 7px; }

  .contacts {
    position: absolute;
    top: 226px;
    list-style: none;
    color: var(--white);
    font-size: 12px;
    line-height: 15.5px;
  }
  .contacts-phones { left: 19px; }
  .contacts-web { left: 148px; }
  .contacts li { display: flex; align-items: center; gap: 9px; }
  .contacts svg { width: 10px; height: 10px; fill: var(--soft-text); flex: none; }
</style>
</head>
<body>

<section class="card card-front" aria-label="Card front">
  <div class="wordmark">
    <span class="wordmark-name">Brenwick</span>
    <span class="wordmark-tag">Casing Services</span>
  </div>
</section>

<section class="card card-back" aria-label="Card back">
  <svg class="back-art" viewBox="0 0 484 292" preserveAspectRatio="none" aria-hidden="true">
    <path fill="var(--brand-red)" d="M112,0 C175,0 200,120 290,156 C360,184 420,200 484,208 L484,0 Z"/>
    <path fill="var(--paper)" d="M148,0 C205,0 222,112 302,150 C362,178 420,198 484,205 L484,0 Z"/>
  </svg>

  <div class="wordmark">
    <span class="wordmark-name">Brenwick</span>
    <span class="wordmark-tag">Casing Services</span>
  </div>

  <div class="person">
    <p class="person-name">Cody Harlan</p>
    <p class="person-title">Area Manager</p>
  </div>

  <ul class="contacts contacts-phones">
    <li>
      <svg viewBox="0 0 10 10"><path d="M2 0.5 L3.6 0.5 L4.2 3 L3 3.8 C3.6 5.2 4.8 6.4 6.2 7 L7 5.8 L9.5 6.4 L9.5 8 C9.5 9 8.8 9.5 8 9.5 C4 9.2 0.8 6 0.5 2 C0.5 1.2 1 0.5 2 0.5Z"/></svg>
      (555) 210-4800
    </li>
    <li>
      <svg viewBox="0 0 10 10"><path d="M0.5 3 C0.5 1.5 2.5 1 5 1 C7.5 1 9.5 1.5 9.5 3 L9.5 4 L7 4 L7 3 L3 3 L3 4 L0.5 4Z M2 5 L8 5 L9 9 L1 9Z"/></svg>
      (555) 318-6625
    </li>
    <li>
      <svg viewBox="0 0 10 10"><path d="M2.5 0.5 L7.5 0.5 L7.5 3 L2.5 3Z M0.5 3.5 L9.5 3.5 L9.5 7.5 L8 7.5 L8 6 L2 6 L2 7.5 L0.5 7.5Z M2.5 6.5 L7.5 6.5 L7.5 9.5 L2.5 9.5Z"/></svg>
      (555) 210-4830
    </li>
  </ul>

  <ul class="contacts contacts-web">
    <li>
      <svg viewBox="0 0 10 10"><path d="M5 0.3 C7.2 0.3 8.6 2 8.6 3.8 C8.6 6.2 5 9.7 5 9.7 C5 9.7 1.4 6.2 1.4 3.8 C1.4 2 2.8 0.3 5 0.3Z M5 2.4 A1.4 1.4 0 1 0 5 5.2 A1.4 1.4 0 1 0 5 2.4Z"/></svg>
      Redmesa, OK 73000
    </li>
    <li>
      <svg viewBox="0 0 10 10"><path d="M0.5 2 L9.5 2 L5 5.5Z M0.5 3.2 L5 6.7 L9.5 3.2 L9.5 8.5 L0.5 8.5Z"/></svg>
      codyharlan@brenwickcs.com
    </li>
    <li>
      <svg viewBox="0 0 10 10"><path d="M5 0.5 A4.5 4.5 0 1 0 5 9.5 A4.5 4.5 0 1 0 5 0.5Z M5 1.5 C4.3 2.3 4 3.6 4 4.5 L1.6 4.5 C1.8 3 3.2 1.7 5 1.5Z M5 1.5 C6.8 1.7 8.2 3 8.4 4.5 L6 4.5 C6 3.6 5.7 2.3 5 1.5Z M1.6 5.5 L4 5.5 C4 6.4 4.3 7.7 5 8.5 C3.2 8.3 1.8 7 1.6 5.5Z M6 5.5 L8.4 5.5 C8.2 7 6.8 8.3 5 8.5 C5.7 7.7 6 6.4 6 5.5Z"/></svg>
      www.brenwickcs.com
    </li>
  </ul>
</section>

</body>
</html>
```